Business Recognition Design

We need a design for a recognition to be given to business leaders in our community.
The recognition shall be made on a brass plaque on wood panel background (picture attached, please use it as a background), and all drawing must be in vectors and only one color (black).
It should also have a logo on the top and signature on the right bottom.
The text is enclosed in DOC file.
Updates

Reason: just to be able to find the best solution

Reason: None of the suggestion is good enough. Logo in general is too big in comparison with the rest of the plate.

Industry/Entity Type

Business

Requirements
Must have
• - standard Windows font (or possibility to install the same font on Windows), as the name on the recognition shall be printed in the same font
Nice to have
• - some graphic element (in curves) representing achievements in business
- should look great :)

```html
<!DOCTYPE html>
<html lang="de">
<head>
<meta charset="utf-8">
<title>Auszeichnung – Unternehmer Deutschlands 2013</title>
<link rel="stylesheet" href="https://fonts.googleapis.com/css2?family=Arimo:wght@400;700&display=swap">
<style>
  :root {
    --page-bg: #e9e7e3;
    --wood-dark: #4a2c14;
    --wood-mid: #6e4523;
    --wood-light: #8a5a31;
    --brass-light: #f3d77a;
    --brass-mid: #d9b04a;
    --brass-dark: #b78a2a;
    --brass-edge: #9c7420;
    --ink: #0d0b08;
    --screw: #c99a3a;
    --screw-hi: #f7df8e;
  }
  * { margin: 0; padding: 0; box-sizing: border-box; }
  html, body {
    width: 1200px; height: 832px; overflow: hidden;
    background: var(--page-bg);
    font-family: "Arimo", Arial, sans-serif;
    color: var(--ink);
  }
  .canvas { position: relative; width: 1200px; height: 832px; }

  .plaque {
    position: absolute; left: 172px; top: 33px;
    width: 856px; height: 660px;
    background: linear-gradient(135deg, var(--wood-light), var(--wood-mid) 45%, var(--wood-dark));
    border-radius: 4px;
  }
  .plate {
    position: absolute; left: 38px; top: 35px;
    width: 780px; height: 592px;
    background: linear-gradient(170deg, var(--brass-light), var(--brass-mid) 40%, var(--brass-dark) 80%, var(--brass-mid));
    border: 2px solid var(--brass-edge);
  }
  .screw {
    position: absolute; width: 18px; height: 18px; border-radius: 50%;
    background: radial-gradient(circle at 35% 35%, var(--screw-hi), var(--screw) 60%, var(--brass-edge));
  }
  .screw--tl { left: 14px; top: 21px; }
  .screw--tr { left: 747px; top: 21px; }
  .screw--bl { left: 14px; top: 548px; }
  .screw--br { left: 747px; top: 548px; }

  .line { position: absolute; left: 58px; white-space: nowrap; line-height: 1; }
  .brand { left: 61px; top: 91px; font-size: 36px; font-weight: 700; letter-spacing: -0.5px; }
  .title { top: 149px; font-size: 38px; font-weight: 400; }
  .honour { font-size: 30px; font-weight: 700; }
  .honour--1 { top: 198px; }
  .honour--2 { top: 235px; }
  .for { top: 269px; font-size: 21px; }
  .recipient { top: 298px; font-size: 25px; font-weight: 700; }
  .citation { font-size: 18px; }
  .citation--1 { top: 340px; }
  .citation--2 { top: 368px; }
  .citation--3 { top: 397px; }
  .citation--4 { top: 428px; }
  .citation .lead { font-size: 20px; font-weight: 700; }
  .citation .lead-small { font-size: 13px; font-weight: 700; }
  .signoff { top: 530px; font-size: 18px; }

  .achievement-figure {
    position: absolute; left: 535px; top: 98px;
    width: 192px; height: 410px;
  }
</style>
</head>
<body>
<div class="canvas">
  <div class="plaque">
    <div class="plate">
      <span class="screw screw--tl"></span>
      <span class="screw screw--tr"></span>
      <span class="screw screw--bl"></span>
      <span class="screw screw--br"></span>

      <div class="line brand">Stiftwerk</div>
      <div class="line title">AUSZEICHNUNG</div>
      <div class="line honour honour--1">als herausragendster</div>
      <div class="line honour honour--2">Unternehmer Deutschlands 2013</div>
      <div class="line for">für</div>
      <div class="line recipient">Herrn Dipl.-Kfm. Max Muster</div>
      <div class="line citation citation--1">Unter der Leitung von <span class="lead">Herr Dipl.-Kfm.</span> <span class="lead-small">Max Muster</span></div>
      <div class="line citation citation--2">hat sich die FIRMA GmbH im Jahr 2013 unter</div>
      <div class="line citation citation--3">den ersten 5% der größten deutschen</div>
      <div class="line citation citation--4">Wirtschaftsunternehmen platziert.</div>
      <div class="line signoff">Lindhofen, 20. Juni 2013 Katrin Vollmer</div>

      <svg class="achievement-figure" role="img" aria-label="Schwarze Silhouette eines jubelnden Mannes mit erhobenen Armen, der auf einer offenen Hand steht" viewBox="0 0 192 410">
        <rect width="192" height="410" fill="var(--ink)" opacity="0.85"/>
      </svg>
    </div>
  </div>
</div>
</body>
</html>
```